Web Developer Needs a Business Card Design

I need a personal business card design that represents me as a web developer for potential employers. I would like the background to be a dark color on the front for contrast with my logo and name. The back will have all my information along with a smaller version of the logo. I want something with a modern look and feel, not too conservative. This will be used for potential employers and freelance work.

Industry/Entity Type

Business

Contact Information for Business Card

Front should have my logo and name. The back should have all my personal information which would include: name: Tom Varulek, phone: 570-614-3098, email: tomvarulek@quillbox.net, website url: www.tomvarulek.net, logo, web developer.

Font styles to use
Sans Serif

Requirements
Must have
• Must include my logo. The color palette base color will be the logo color.

```html
<!DOCTYPE html>
<html lang="en">
<head>
<meta charset="utf-8">
<title>Tom Varulek – Business Card</title>
<link rel="stylesheet" href="https://fonts.googleapis.com/css2?family=Open+Sans:wght@300;400;600;700&display=swap">
<style>
  :root {
    --teal: #6fcfbb;
    --teal-dark: #4fb7a3;
    --ink: #111111;
    --paper: #ffffff;
    --text: #1d1d1d;
    --backdrop: #e8e5e1;
  }
  * { box-sizing: border-box; margin: 0; padding: 0; }
  html, body { width: 1200px; height: 913px; overflow: hidden; }
  body {
    background: var(--backdrop);
    font-family: "Open Sans", Arial, sans-serif;
    color: var(--text);
    position: relative;
  }
  .card {
    position: absolute;
    top: 302px;
    width: 540px;
    height: 308px;
    border-radius: 18px;
    overflow: hidden;
    background: var(--paper);
    box-shadow: 0 10px 28px rgba(0,0,0,0.18);
  }
  .card--contact { left: 40px; }
  .card--identity { left: 620px; }
  .card__art { position: absolute; inset: 0; width: 100%; height: 100%; }

  .brand-mark {
    position: absolute;
    display: flex;
    flex-direction: column;
    align-items: center;
    gap: 10px;
  }
  .brand-mark__dot {
    width: 78px; height: 78px;
    border-radius: 50%;
    border: 8px solid var(--teal);
  }
  .brand-mark__name {
    font-weight: 600;
    font-size: 22px;
    color: var(--teal);
    letter-spacing: 1px;
  }
  .card--contact .brand-mark { left: 70px; top: 92px; width: 150px; }

  .contact {
    position: absolute;
    right: 22px;
    top: 92px;
    text-align: right;
  }
  .contact__name {
    font-weight: 700;
    font-size: 20px;
    letter-spacing: 0.5px;
    color: var(--text);
    line-height: 1.1;
  }
  .contact__role {
    font-weight: 400;
    font-size: 12px;
    letter-spacing: 1px;
    color: var(--teal-dark);
    margin-bottom: 14px;
  }
  .contact__line {
    display: flex;
    justify-content: flex-end;
    align-items: center;
    gap: 6px;
    font-size: 13.5px;
    line-height: 1.55;
  }
  .contact__icon { width: 12px; height: 12px; flex: none; }

  .card--identity .brand-mark { left: 0; right: 0; top: 50px; }
  .identity__name {
    position: absolute;
    left: 0; right: 0; top: 178px;
    text-align: center;
    font-weight: 300;
    font-size: 34px;
    letter-spacing: 3px;
    color: var(--text);
  }
  .identity__role {
    position: absolute;
    left: 0; right: 0; top: 228px;
    text-align: center;
    font-size: 17px;
    color: var(--text);
  }
</style>
</head>
<body>

  <section class="card card--contact">
    <svg class="card__art" viewBox="0 0 540 308" preserveAspectRatio="none" aria-hidden="true">
      <rect width="540" height="308" fill="#ffffff"/>
      <path d="M0 0 H360 C285 40 275 140 265 200 C255 262 205 292 140 308 H0 Z" fill="#6fcfbb" stroke="#111" stroke-width="2"/>
      <path d="M0 0 H338 C262 40 252 140 242 200 C232 262 182 292 118 308 H0 Z" fill="#111111"/>
    </svg>

    <div class="brand-mark">
      <div class="brand-mark__dot"></div>
      <div class="brand-mark__name">Varulek</div>
    </div>

    <div class="contact">
      <div class="contact__name">TOM VARULEK</div>
      <div class="contact__role">WEB DEVELOPER</div>
      <div class="contact__line">570-614-3098
        <svg class="contact__icon" viewBox="0 0 12 12"><path d="M2.5 1 L4.5 1 L5.3 3.6 L4 4.6 C4.7 6 6 7.3 7.4 8 L8.4 6.7 L11 7.5 L11 9.5 C11 10.4 10.3 11 9.5 11 C5 10.7 1.3 7 1 2.5 C1 1.7 1.6 1 2.5 1 Z" fill="#4fb7a3"/></svg>
      </div>
      <div class="contact__line">tomvarulek@quillbox.net
        <svg class="contact__icon" viewBox="0 0 12 12"><rect x="1" y="2.5" width="10" height="7" rx="1" fill="none" stroke="#4fb7a3" stroke-width="1.3"/><path d="M1.5 3 L6 6.5 L10.5 3" fill="none" stroke="#4fb7a3" stroke-width="1.3"/></svg>
      </div>
      <div class="contact__line">www.tomvarulek.net
        <svg class="contact__icon" viewBox="0 0 12 12"><circle cx="6" cy="6" r="5" fill="none" stroke="#4fb7a3" stroke-width="1.2"/><ellipse cx="6" cy="6" rx="2.2" ry="5" fill="none" stroke="#4fb7a3" stroke-width="1"/><path d="M1 6 H11 M2 3.5 H10 M2 8.5 H10" stroke="#4fb7a3" stroke-width="0.9"/></svg>
      </div>
    </div>
  </section>

  <section class="card card--identity">
    <div class="brand-mark">
      <div class="brand-mark__dot"></div>
    </div>
    <div class="identity__name">TOM VARULEK</div>
    <div class="identity__role">Front-End Developer</div>
  </section>

</body>
</html>
```